Landscape Construction and Design Company

We are a landscape construction and design company from New Jersey. We design and install landscapes and hardscapes for residential properties. The name of the company is Belwick's Landscape and Design LLC. We specialize mostly in planting trees and stone work, some water features. We would like to see design themes that include a tree or trees and a stone walkway or wall. We like earth tone colors. We like traditional to modern designs.

Target Market(s)

Homeowners

Industry/Entity Type

Landscape

Contact Information for Business Card

Nature themed design, earth tone colors, space for company name, address, phone numbers, email and website address

Logo Text

No text

Font styles to use
Serif

Colors

Designer to choose colors to be used in the design.

Requirements
Must have
• A tree or trees, similar to the ones uploaded in my supporting images
Nice to have
• I like trees similar to those in my uploaded supporting images. I like artistic, nature theme, earth tone colors
Should not have
• Pictures of real landscapes, cartoon looking logo or objects

```html
<!DOCTYPE html>
<html lang="en">
<head>
<meta charset="utf-8">
<title>Belwick's Landscape and Design LLC – Business Card</title>
<link rel="stylesheet" href="https://fonts.googleapis.com/css2?family=Cinzel:wght@400;500&family=Source+Sans+3:wght@400;600&display=swap">
<style>
  :root {
    --backdrop: #2d2d2d;
    --card-front: #ffffff;
    --card-back: #37602e;
    --leaf-green: #5e9f2c;
    --leaf-light: #9ccd4f;
    --mark-soft: #a9d46a;
    --ink: #1d1d1d;
    --rule: #8d8daa;
    --back-text: #eef3e6;
  }
  * { margin: 0; padding: 0; box-sizing: border-box; }
  html, body { width: 1200px; height: 900px; overflow: hidden; background: var(--backdrop); }
  .canvas { position: relative; width: 1200px; height: 900px; }
  .card { position: absolute; top: 170px; width: 347px; height: 561px; }
  .card--front { left: 259px; background: var(--card-front); }
  .card--back { left: 631px; background: var(--card-back); }

  .tree-mark { position: absolute; left: 50%; transform: translateX(-50%); border-radius: 50%; }
  .card--front .tree-mark { top: 50px; width: 220px; height: 220px;
    background: radial-gradient(circle at 50% 45%, var(--leaf-light), var(--leaf-green)); }
  .card--back .tree-mark { top: 118px; width: 150px; height: 150px;
    background: radial-gradient(circle at 50% 45%, var(--mark-soft), var(--leaf-green)); }

  .contact { position: absolute; top: 338px; left: 0; width: 100%; text-align: center;
    font-family: "Source Sans 3", sans-serif; font-size: 15px; color: var(--ink); line-height: 1.35; }
  .contact__name { font-family: "Cinzel", serif; font-weight: 400; font-size: 23px;
    color: var(--leaf-green); letter-spacing: 0.5px; line-height: 1.1; }
  .contact__role { margin-top: 2px; }
  .contact__rule { width: 157px; height: 1px; background: var(--rule); margin: 12px auto 9px; }
  .contact__label { color: var(--leaf-green); font-weight: 600; }
  .contact__web { color: var(--leaf-green); font-weight: 600; }
  .contact p { margin: 2px 0; }

  .brand { position: absolute; top: 292px; left: 20px; right: 20px; text-align: center;
    font-family: "Cinzel", serif; font-weight: 500; font-size: 27px; line-height: 1.2;
    color: var(--leaf-light); }
  .services { position: absolute; top: 472px; left: 0; width: 100%; text-align: center;
    font-family: "Source Sans 3", sans-serif; font-size: 17px; line-height: 1.25;
    color: var(--back-text); text-transform: uppercase; letter-spacing: 0.3px; }
</style>
</head>
<body>
<main class="canvas">
  <section class="card card--front">
    <div class="tree-mark" role="img" aria-label="Company tree emblem with green leaf canopy and brown trunk"></div>
    <div class="contact">
      <h1 class="contact__name">DANIEL HARLOW</h1>
      <p class="contact__role">Managing Director</p>
      <div class="contact__rule"></div>
      <p><span class="contact__label">P:</span> 823-555-0142</p>
      <p><span class="contact__label">E:</span> info@belwicklandscape.com</p>
      <p class="contact__web">www.belwicklandscape.com</p>
      <div class="contact__rule"></div>
      <p>1234, Address Goes Here<br>Country Name, 123456</p>
    </div>
  </section>

  <section class="card card--back">
    <div class="tree-mark" role="img" aria-label="Company tree emblem"></div>
    <h2 class="brand">Belwick's Landscape and Design LLC</h2>
    <p class="services">Planting Trees<br>Stone Work | Water Features</p>
  </section>
</main>
</body>
</html>
```